Webdesign for large cottage directory

We have developed a first version of a website that can accommodate large groups (10 to 300 people). The site is English and is aimed at a wide audience ranging from a group of students to a family or a family. For the visitors the site is free and it is the propietaires who pay to see their accommodation. The site is online with just a few fake lodgings and a simple design to the elements that must be appraised (nothing to keep the current design). Our website is here: 9lodgia.com (login / pass = admin / 123) Home page (9lodgia.com): on this page section) and lodging by theme (third section). These three points should be highlighted as possible. The displayed map may be slightly modified. Only the background and the color changes when hovering over the mouse. It can be enlarged / retreciated. Below these 3 sections we have some fairly published articles, the latest blog posts and the footer. The menu will be visible throughout the site. Category page (https://9lodgia.fr/gite-departement/aveyron OR https://9lodgia.fr/gites-couchages-121): On these pages we always return the same format with the googlemap, an image 1 text. Below the list of the cottages concerned and the filter options. Product page: The pages presenting the cottages can be of two types: - Either the cottage has no owner and there is no contact for the visitor to the owner that he can retrieve his cottage by registering: example of a page of this type: https://9lodgia.fr/domaine-de-vercasse - The cottage to a propietaire and we are on the classic card. : // 9lodgia. en / domain-of-vercasse2 For all products on the site we have nav tab. It's just for testing. We do not want to be in the design for real website. All information must be in the page without login / register page: classic, it's here: https://9lodgia.it/login and https://9lodgia.fr/register Blog homepage (https://9lodgia.fr/blog ): Classic blog page Blog post (https://9lodgia.fr/blog/urltemporaire1551521154) and static page (https://9lodgia.fr/blog/Systeme-classement-9lodgiafr): Nothing special Menu: Menu is an important part of the website. It's the way to navigate on the wbesite.
Faible participation designers
4 page

```html
<!DOCTYPE html>
<html lang="en">
<head>
<meta charset="utf-8">
<title>9lodgia.Fr — Large Cottage Directory</title>
<link rel="stylesheet" href="https://fonts.googleapis.com/css2?family=Nunito+Sans:wght@400;600;700;800;900&display=swap">
<style>
:root{
  --blue:#0a7cff;
  --blue-dark:#0563d4;
  --ink:#111418;
  --muted:#6b6f76;
  --line:#c9cdd3;
  --soft:#f2f2f2;
  --white:#ffffff;
  --map:#a89fe0;
  --footer:#1d1d1f;
  --footer-text:#d0d0d0;
}
*{box-sizing:border-box;margin:0;padding:0}
html,body{width:1200px;height:4390px;overflow:hidden}
body{font-family:"Nunito Sans",Arial,sans-serif;color:var(--ink);background:var(--white);position:relative}
a{color:inherit;text-decoration:none}

/* Header */
.site-header{position:absolute;top:0;left:0;width:1200px;height:80px;background:var(--white);display:flex;align-items:center;padding:0 111px;justify-content:space-between}
.brand{font-size:26px;font-weight:800;color:var(--blue)}
.main-nav{display:flex;gap:22px;font-size:15px;color:#333;font-weight:600}
.main-nav span.has-sub::after{content:" ›";font-size:12px}

/* Hero */
.hero{position:absolute;top:80px;left:0;width:1200px;height:600px;text-align:center;color:var(--white)}
.hero-photo{position:absolute;inset:0;background:linear-gradient(180deg,#5d55b8 0%,#7c79c9 38%,#9a92c7 55%,#8a6c5c 70%,#5c6a3e 85%,#3f4a2c 100%)}
.hero-content{position:relative;padding-top:92px}
.hero h1{font-size:56px;font-weight:900;letter-spacing:-.5px}
.hero p{font-size:18px;font-weight:700;line-height:30px;width:640px;margin:22px auto 0}
.btn-primary{display:inline-block;background:var(--blue);color:var(--white);font-weight:800;font-size:17px;width:207px;height:56px;line-height:56px;border-radius:28px;margin-top:30px}

/* Section headings */
.section-title{font-size:34px;font-weight:800;text-align:center;position:absolute;left:0;width:1200px}

/* Capacity */
.capacity{position:absolute;top:680px;left:0;width:1200px;height:505px;background:var(--white)}
.capacity .section-title{top:68px}
.cap-cards{position:absolute;top:180px;left:111px;display:flex;gap:21px}
.cap-card{width:178px;height:210px;border:1px solid var(--line);background:var(--white);text-align:center;padding-top:45px}
.cap-card .ring{width:80px;height:80px;border:2px solid #9aa0a8;border-radius:50%;margin:0 auto;line-height:76px;font-size:19px;font-weight:700;color:#555}
.cap-card .label{font-size:15px;font-weight:700;margin-top:22px;color:#333}
.cap-card.active{background:var(--blue);border-color:var(--blue)}
.cap-card.active .ring{border-color:var(--white);color:var(--white)}
.cap-card.active .label{color:var(--white)}
.slider-arrow{position:absolute;top:263px;width:46px;height:46px;border-radius:50%;background:#6e6e72;display:flex;align-items:center;justify-content:center}
.slider-arrow.prev{left:50px}
.slider-arrow.next{left:1102px}

/* Department */
.department{position:absolute;top:1185px;left:0;width:1200px;height:660px;background:var(--soft)}
.department .section-title{top:62px}
.map-area{position:absolute;top:153px;left:181px;width:838px;height:427px;background:radial-gradient(ellipse at 45% 45%,#ecebe9 0 22%,var(--map) 23%)}
.map-compass{position:absolute;top:20px;right:20px;width:44px;height:44px;border:3px solid #2c2c44;border-radius:50%;background:#d4d0ef}
.map-zoom{position:absolute;right:22px;bottom:28px;width:26px;background:var(--white);border-radius:3px;font-size:16px;font-weight:800;text-align:center;color:#444;line-height:24px}
.map-zoom span{display:block;border-bottom:1px solid #ddd}

/* Theme */
.themes{position:absolute;top:1845px;left:0;width:1200px;height:1230px;background:var(--white)}
.themes .section-title{top:68px}
.theme-tile{position:absolute;overflow:hidden}
.theme-tile .name{position:absolute;left:18px;bottom:14px;color:var(--white);font-size:21px;font-weight:700}
.pagination{position:absolute;top:1118px;left:439px;display:flex;border:1px solid #d6d6d6}
.pagination span{width:47px;height:45px;display:flex;align-items:center;justify-content:center;font-size:17px;color:#555;border-right:1px solid #d6d6d6;font-weight:700}
.pagination span:last-child{border-right:0}
.pagination .current{background:var(--blue);color:var(--white)}
.pagination .page{background:#eaf0fb;color:#8a97ad}

/* Banner */
.cta-banner{position:absolute;top:3075px;left:0;width:1200px;height:205px;background:linear-gradient(90deg,#6d7a5a 0%,#8aa0b5 15%,var(--blue) 36%,var(--blue) 100%);color:var(--white)}
.cta-banner p{position:absolute;left:300px;top:64px;width:480px;text-align:center;font-size:21px;font-weight:600;line-height:38px}
.cta-side{position:absolute;left:813px;top:32px;width:276px;text-align:center}
.cta-side h3{font-size:32px;font-weight:800}
.btn-white{display:block;margin-top:22px;background:var(--white);color:var(--blue);font-weight:800;font-size:17px;height:56px;line-height:56px;border-radius:28px}

/* Blog */
.blog{position:absolute;top:3280px;left:0;width:1200px;height:665px}
.blog .section-title{top:72px}
.post{position:absolute;top:168px;width:310px}
.post-photo{height:193px}
.post-head{display:flex;gap:14px;margin-top:19px}
.post-date{width:40px;height:46px;background:var(--blue);color:var(--white);text-align:center;font-size:14px;font-weight:800;line-height:16px;padding-top:6px;flex:none}
.post-date small{display:block;font-size:12px;font-weight:600}
.post-title{font-size:21px;font-weight:600;line-height:26px;color:#222}
.post-excerpt{font-size:14px;line-height:22px;color:var(--muted);margin-top:20px}
.btn-outline{display:inline-block;margin-top:16px;width:147px;height:43px;line-height:39px;border:2px solid #333;border-radius:22px;text-align:center;font-weight:800;font-size:14px}

/* Footer */
.site-footer{position:absolute;top:3945px;left:0;width:1200px;height:445px;background:var(--footer);color:var(--footer-text)}
.f-col{position:absolute;top:62px}
.f-col h4{color:var(--white);font-size:21px;font-weight:800;margin-bottom:26px}
.f-col p{font-size:13px;line-height:23px}
.f-about{left:111px;width:300px}
.f-news{left:503px;width:290px}
.f-contact{left:843px;width:250px}
.news-input{margin-top:18px;height:36px;border:2px solid var(--white);border-radius:18px;font-size:12px;padding-left:18px;line-height:32px;color:#ccc;width:270px}
.btn-subscribe{display:block;margin-top:16px;width:143px;height:38px;line-height:38px;border-radius:19px;background:var(--blue);color:var(--white);font-size:14px;font-weight:800;text-align:center}
.contact-row{display:flex;gap:18px;font-size:14px;line-height:22px;margin-bottom:20px}
.contact-row svg{flex:none;margin-top:3px}
.social{position:absolute;top:4312px;left:0;width:1200px;display:flex;justify-content:center;gap:8px}
.social{top:365px}
.social span{width:26px;height:26px;border:2px solid #cfcfcf;border-radius:50%}
.copyright{position:absolute;top:410px;width:1200px;text-align:center;font-size:14px;color:#d5d5d5}
</style>
</head>
<body>

<header class="site-header">
  <a class="brand" href="#">9lodgia.Fr</a>
  <nav class="main-nav">
    <span class="has-sub">Cottage By Capacity</span>
    <span class="has-sub">Cottage By Department</span>
    <span class="has-sub">Lodging By Theme</span>
    <span>Blog</span>
    <span>Your Favorites</span>
    <span class="has-sub">Owner's Area</span>
  </nav>
</header>

<section class="hero">
  <div class="hero-photo" role="img" aria-label="Row of colourful wooden beach houses under a purple evening sky"></div>
  <div class="hero-content">
    <h1>Welcome to 9lodgia.Fr</h1>
    <p>Duis aute irure dolor in reprehenderit in voluptate velit esse cillum dolore eu fugiat nulla pariatur.</p>
    <a class="btn-primary" href="#">READ MORE</a>
  </div>
</section>

<section class="capacity">
  <h2 class="section-title">Lodging By Capacity</h2>
  <div class="slider-arrow prev"><svg width="14" height="14" viewBox="0 0 14 14"><path d="M9 2 4 7l5 5" stroke="#fff" stroke-width="2.4" fill="none"/></svg></div>
  <div class="cap-cards">
    <div class="cap-card"><div class="ring">1- 20</div><div class="label">2 to 20 People</div></div>
    <div class="cap-card"><div class="ring">1- 20</div><div class="label">20 to 40 People</div></div>
    <div class="cap-card active"><div class="ring">1- 20</div><div class="label">40 to 60 People</div></div>
    <div class="cap-card"><div class="ring">1- 20</div><div class="label">60 to 80 People</div></div>
    <div class="cap-card"><div class="ring">1- 20</div><div class="label">80 to 120 People</div></div>
  </div>
  <div class="slider-arrow next"><svg width="14" height="14" viewBox="0 0 14 14"><path d="M5 2l5 5-5 5" stroke="#fff" stroke-width="2.4" fill="none"/></svg></div>
</section>

<section class="department">
  <h2 class="section-title">Lodging By Department</h2>
  <div class="map-area" role="img" aria-label="Interactive map of France divided into departments">
    <div class="map-compass"></div>
    <div class="map-zoom"><span>+</span><span>−</span><span style="border:0">·</span></div>
  </div>
</section>

<section class="themes">
  <h2 class="section-title">Lodging By Theme</h2>
  <div class="theme-tile" style="left:158px;top:157px;width:281px;height:188px;background:linear-gradient(160deg,#b0612a,#3a1e14 70%)" role="img" aria-label="Audience at a seminar"><span class="name">Seminar</span></div>
  <div class="theme-tile" style="left:158px;top:365px;width:281px;height:372px;background:linear-gradient(180deg,#e8ecf0,#a89a86 55%,#5b4a3a)" role="img" aria-label="Horse jumping over a fence"><span class="name">Horse Riding</span></div>
  <div class="theme-tile" style="left:158px;top:757px;width:281px;height:188px;background:linear-gradient(180deg,#f2a55c,#c45a2e 55%,#3c2a2a)" role="img" aria-label="Snowy mountain peaks at sunset"><span class="name">Snow Nature</span></div>

  <div class="theme-tile" style="left:460px;top:157px;width:281px;height:375px;background:linear-gradient(180deg,#d4b48a,#7a7a70 50%,#2c3a45)" role="img" aria-label="Suspension bridge over water at dusk"><span class="name">Peach</span></div>
  <div class="theme-tile" style="left:460px;top:552px;width:281px;height:185px;background:linear-gradient(160deg,#3d6fa8,#2a4f7a 60%,#1e2a36)" role="img" aria-label="Mountain biker on a trail"><span class="name">Mountain Bike</span></div>
  <div class="theme-tile" style="left:460px;top:757px;width:281px;height:261px;background:linear-gradient(180deg,#c9b49a,#7b5f48 55%,#2e241c)" role="img" aria-label="Group of friends celebrating together"><span class="name">Integration Weekend</span></div>

  <div class="theme-tile" style="left:761px;top:157px;width:281px;height:281px;background:linear-gradient(180deg,#2f9e9c,#1f6f7c 60%,#174a57)" role="img" aria-label="Sea turtle swimming underwater"><span class="name">Aquatic</span></div>
  <div class="theme-tile" style="left:761px;top:458px;width:281px;height:188px;background:linear-gradient(160deg,#8cb44c,#3d6e2a 60%,#25401c)" role="img" aria-label="Children at a summer camp in the forest"><span class="name">Summer Camp</span></div>
  <div class="theme-tile" style="left:761px;top:665px;width:281px;height:207px;background:linear-gradient(160deg,#a8845a,#5c4630 60%,#2a2018)" role="img" aria-label="Table set with shared gourmet dishes"><span class="name">Gastronomic</span></div>

  <nav class="pagination">
    <span>⏮</span><span>‹</span><span class="current">1</span><span class="page">2</span><span class="page">3</span><span>›</span><span>⏭</span>
  </nav>
</section>

<section class="cta-banner">
  <div style="position:absolute;left:0;top:0;width:300px;height:205px;background:linear-gradient(90deg,#6b7554,rgba(107,117,84,0))" role="img" aria-label="Cottages by a lake"></div>
  <p>Duis aute irure dolor in reprehenderit in voluptate velit esse cillum</p>
  <div class="cta-side">
    <h3>9lodgia.Fr</h3>
    <a class="btn-white" href="#">View Cottage Directory</a>
  </div>
</section>

<section class="blog">
  <h2 class="section-title">Latest Blog</h2>
  <article class="post" style="left:111px">
    <div class="post-photo" role="img" aria-label="Resort pool lit at night" style="background:linear-gradient(180deg,#1c3a6a,#2a5a7a 55%,#c8902a)"></div>
    <div class="post-head"><div class="post-date">29<small>Mar</small></div><h3 class="post-title">At vero eos et accusamus et iusto odio</h3></div>
    <p class="post-excerpt">Lorem ipsum dolor sit amet, consectetur adipisicing elit, sed do eiusmod tempor incididunt ut labore et dolore.</p>
    <a class="btn-outline" href="#">READ MORE</a>
  </article>
  <article class="post" style="left:445px">
    <div class="post-photo" role="img" aria-label="Colourful beach huts under palm trees" style="background:linear-gradient(180deg,#8fc2e6,#4f9a62 50%,#d98a5a)"></div>
    <div class="post-head"><div class="post-date">29<small>Mar</small></div><h3 class="post-title">At vero eos et accusamus et iusto odio</h3></div>
    <p class="post-excerpt">Lorem ipsum dolor sit amet, consectetur adipisicing elit, sed do eiusmod tempor incididunt ut labore et dolore.</p>
    <a class="btn-outline" href="#">READ MORE</a>
  </article>
  <article class="post" style="left:779px">
    <div class="post-photo" role="img" aria-label="Wooden cabin among tall forest trees" style="background:linear-gradient(180deg,#4f7a3a,#3a5a2c 55%,#8a5a34)"></div>
    <div class="post-head"><div class="post-date">29<small>Mar</small></div><h3 class="post-title">At vero eos et accusamus et iusto odio</h3></div>
    <p class="post-excerpt">Lorem ipsum dolor sit amet, consectetur adipisicing elit, sed do eiusmod tempor incididunt ut labore et dolore.</p>
    <a class="btn-outline" href="#">READ MORE</a>
  </article>
</section>

<footer class="site-footer">
  <div class="f-col f-about">
    <h4>About Us</h4>
    <p>Nemo enim ipsam voluptatem quia voluptas sit aspernatur aut odit aut fugit, sed quia consequuntur magni dolores eos qui ratione voluptatem sequi nesciunt. Neque porro quisquam est, qui dolorem ipsum quia dolor sit amet, consectetur, adipisci velit, sed quia non numquam eius modi tempora incidunt ut labore et dolore magnam aliquam quaerat voluptatem.</p>
  </div>
  <div class="f-col f-news">
    <h4>Sign Up For Newsletter</h4>
    <p>excepteur sint occaecat cupidatat non proident, sunt in culpa qui officia deserunt</p>
    <div class="news-input">Enter email</div>
    <a class="btn-subscribe" href="#">SUBSCRIBE</a>
  </div>
  <div class="f-col f-contact">
    <h4>Contact Us</h4>
    <div class="contact-row"><svg width="16" height="20" viewBox="0 0 16 20"><path d="M8 0a7 7 0 0 0-7 7c0 5 7 13 7 13s7-8 7-13a7 7 0 0 0-7-7zm0 10a3 3 0 1 1 0-6 3 3 0 0 1 0 6z" fill="#fff"/></svg><span>218 Harbor Lane Suite 40, Millbrook, OR 97021</span></div>
    <div class="contact-row"><svg width="16" height="16" viewBox="0 0 16 16"><path d="M3 1l3 3-2 2c1 2 3 4 5 5l2-2 3 3-2 3C6 15 1 10 1 3z" fill="#fff"/></svg><span>Phone:<br>(555) 014-2387</span></div>
    <div class="contact-row"><svg width="16" height="13" viewBox="0 0 16 13"><rect width="16" height="13" rx="1" fill="#fff"/><path d="M1 1l7 6 7-6" stroke="#1d1d1f" stroke-width="1.5" fill="none"/></svg><span>Email:<br>info@9lodgia.com</span></div>
  </div>
  <div class="social"><span></span><span></span><span></span><span></span></div>
  <p class="copyright">9lodgia © 2019 | All Rights Reserved</p>
</footer>

</body>
</html>
```